Harborview Estates Business Card for Apartment Buildings

Create business cards for resident managers who run apartment buildings. The audience is the public who are searching for apartment rentals, and current residents who live at the apartment building. Key design element will be incorporating the company logo, however, the logo cannot dominate. The building name and manager name are more important than the logo. Current business card design leaves little room for copy, so we may need to reduce the size on the current card to allow for more space for copy.

Target Market(s)

Adults 18-65 years of age, who are looking for an apartment rental, plus current residents who live at our apartment buildings.

Industry/Entity Type

Property Management

Contact Information for Business Card

A major design element will be use of the company logo. Important property and manager contact information must be part of the design. The size of the logo will need to be reduced to make room for building and manager contact copy.

Font styles to use
Sans Serif

Colors
3176b5
000000
959595
ffffff

Requirements
Must have
• 1) Incorporate the company logo.
• 2) Use the company colors (dark blue, black/grey, over white).
• 3) FEATURE THE BUILDING NAME
• 4) FEATURE THE MANAGER NAME
• 5) The company name is less important than BUILDING and MANAGER
• 6) Manager contact information
• **SEE ATTACHED CREATIVE BRIEF**
Nice to have
• 1) Back of card logo watermark
• 2) Ability to write notes on back of carfd
Should not have
• Avoid letting the company logo dominate the card, the building name and manager are more important than the company logo.

```html
<!DOCTYPE html>
<html lang="en">
<head>
<meta charset="utf-8">
<title>Harborview Estates Business Card</title>
<link href="https://fonts.googleapis.com/css2?family=Oswald:wght@600&family=Roboto:wght@400;500;700&display=swap" rel="stylesheet">
<style>
  :root {
    --brand-blue: #1f6497;
    --accent-blue: #3176b5;
    --ink: #1a1a1a;
    --grey: #959595;
    --paper: #ffffff;
    --backdrop: #e9eaeb;
  }
  * { margin: 0; padding: 0; box-sizing: border-box; }
  html, body { width: 1200px; height: 726px; overflow: hidden; }
  body {
    background: var(--backdrop);
    font-family: "Roboto", Arial, sans-serif;
    position: relative;
  }
  .card {
    position: absolute;
    width: 540px;
    height: 309px;
    box-shadow: 0 6px 18px rgba(0,0,0,0.18);
  }
  /* Front */
  .card-front {
    left: 40px;
    top: 150px;
    background: var(--brand-blue);
    color: var(--paper);
  }
  .brand-lockup {
    position: absolute;
    left: 0; right: 0;
    top: 100px;
    display: flex;
    align-items: center;
    justify-content: center;
    gap: 14px;
  }
  .brand-dot {
    width: 40px; height: 40px;
    border-radius: 50%;
    background: var(--paper);
    flex: none;
  }
  .brand-name {
    font-weight: 700;
    font-size: 24px;
    line-height: 1.15;
    letter-spacing: 1.5px;
    text-transform: uppercase;
    color: var(--paper);
  }
  .front-web {
    position: absolute;
    left: 0; right: 0;
    bottom: 34px;
    text-align: center;
    font-size: 14px;
    letter-spacing: 0.3px;
  }
  /* Back */
  .card-back {
    left: 620px;
    top: 270px;
    background: var(--paper);
    color: var(--ink);
  }
  .building-name {
    position: absolute;
    left: 34px; top: 24px;
    font-size: 12px;
    font-weight: 500;
    letter-spacing: 1.5px;
    text-transform: uppercase;
    color: var(--grey);
  }
  .manager-name {
    position: absolute;
    left: 34px; top: 46px;
    font-family: "Oswald", "Arial Narrow", sans-serif;
    font-weight: 600;
    font-size: 30px;
    line-height: 1;
    color: var(--brand-blue);
    text-transform: uppercase;
  }
  .manager-role {
    position: absolute;
    left: 34px; top: 82px;
    font-size: 17px;
    color: var(--ink);
  }
  .corner-brand {
    position: absolute;
    right: 30px; top: 78px;
    display: flex;
    align-items: center;
    gap: 8px;
  }
  .corner-square {
    width: 16px; height: 16px;
    background: var(--brand-blue);
  }
  .corner-name {
    font-size: 12px;
    font-weight: 500;
    color: var(--brand-blue);
    text-transform: uppercase;
    letter-spacing: 1px;
  }
  .address {
    position: absolute;
    left: 34px; top: 150px;
    font-size: 13px;
    line-height: 17px;
  }
  .contact-list {
    position: absolute;
    left: 34px; top: 198px;
    list-style: none;
    font-size: 13px;
    line-height: 19px;
  }
  .contact-list li { display: flex; align-items: center; gap: 10px; }
  .contact-icon { width: 13px; height: 13px; flex: none; }
  .web-domain { color: var(--accent-blue); }
</style>
</head>
<body>
  <section class="card card-front" aria-label="Card front">
    <div class="brand-lockup">
      <span class="brand-dot"></span>
      <span class="brand-name">Harborview<br>Estates LLC</span>
    </div>
    <p class="front-web">www.harborviewestates.us</p>
  </section>

  <section class="card card-back" aria-label="Card back">
    <p class="building-name">Lakeside Terrace Apartments</p>
    <h1 class="manager-name">Dana Whitfield</h1>
    <p class="manager-role">Property Manager</p>

    <div class="corner-brand">
      <span class="corner-square"></span>
      <span class="corner-name">Harborview Estates</span>
    </div>

    <p class="address">2750 Lakeside Avenue<br>#B210 Portland, OR 97205</p>

    <ul class="contact-list">
      <li>
        <svg class="contact-icon" viewBox="0 0 16 16"><circle cx="8" cy="8" r="7" fill="none" stroke="#1f6497" stroke-width="1.5"/><path d="M5.5 4.5l1.5 1.5-0.8 1c0.5 1.2 1.3 2 2.5 2.6l1-0.9 1.6 1.4c-0.5 1-1.4 1.3-2.3 1-2.2-0.8-3.8-2.4-4.4-4.6-0.2-0.9 0.1-1.6 0.9-2z" fill="#1f6497"/></svg>
        <span>555-318-4420</span>
      </li>
      <li>
        <svg class="contact-icon" viewBox="0 0 16 16"><rect x="4" y="1.5" width="8" height="4" fill="#1f6497"/><rect x="1.5" y="6" width="13" height="6" rx="1" fill="#1f6497"/><rect x="4" y="10" width="8" height="4.5" fill="#fff" stroke="#1f6497" stroke-width="1.2"/></svg>
        <span>555-318-4471</span>
      </li>
      <li>
        <svg class="contact-icon" viewBox="0 0 16 16"><rect x="1" y="3" width="14" height="10" fill="none" stroke="#1f6497" stroke-width="1.5"/><path d="M1 3.5l7 5 7-5" fill="none" stroke="#1f6497" stroke-width="1.5"/></svg>
        <span>dana@harborviewestates.us</span>
      </li>
      <li>
        <svg class="contact-icon" viewBox="0 0 16 16"><circle cx="8" cy="8" r="6.8" fill="none" stroke="#1f6497" stroke-width="1.4"/><ellipse cx="8" cy="8" rx="3" ry="6.8" fill="none" stroke="#1f6497" stroke-width="1.2"/><path d="M1.2 8h13.6M2.5 4.5h11M2.5 11.5h11" stroke="#1f6497" stroke-width="1.1"/></svg>
        <span>www.<span class="web-domain">harborviewestates.us</span></span>
      </li>
    </ul>
  </section>
</body>
</html>
```